Exciting new website for concierge aesthetic company

Simple, elegant, fresh design for female owned concierge aesthetic company, catering to both men and women ages 30-60. We would like a home page with an exciting catch phrase, a brief description of the company and a section to fill out an appointment request that includes a section for a referral. Please also have a book appointment link in the header of all pages that will link back to booking information form on home page. Separate pages to include:
- Services = 3 different services. Each service stating the name of the service and then providing a brief description. 3 services are "Private Session" for 1 client, "Group Session" for 2-5 clients, "Party" for 6+ clients. Will provide service descriptions text later. Item at bottom of page to allow description of how to "Host a Party".
- Products = 4 different product lines. Will provide pictures of product, brief description and link to manufacturer's website.
- Stories = brief client reviews to include before and after photos
- About us = Personal picture with brief description of owner's fun, exciting and family focussed lifestyle.
*Our domain is registered with varnix and we be using varnix for website hosting.

Target Market(s)

30-60 year old men and women, but mostly women

Industry/Entity Type

beauty and aesthetics

Coding

Coded - Design and coding required

Number of Pages Required

5+ page

Font styles to use
Sans Serif
Script

Colors
59FF00
82FF00
B8FF75
E3FFCB
F4FFEA
FFC000
F8CF3A
FAE287
FDF2CF
FEFAEE
F0912C
F2A743
F7CA91
FBE8D2
FDF5EE
E54698
E96AAD
F1A4CE
F9D9EA
FCEFF6

Requirements
Must have
• coded for varnix
Should not have
• corny pictures. No needles in pictures or graphics. No medical office or medical chair in pictures.

```html
<!DOCTYPE html>
<html lang="en">
<head>
<meta charset="utf-8">
<title>Glow Muse – Concierge Aesthetics</title>
<link href="https://fonts.googleapis.com/css2?family=Dancing+Script:wght@500;700&family=Poppins:wght@400;500&display=swap" rel="stylesheet">
<style>
:root{
  --pink:#dc3590;
  --pink-soft:#f1a4ce;
  --orange:#f0912c;
  --peach:#f7ca91;
  --hero:#d4dae3;
  --dark:#262626;
  --ink:#3a3a3a;
  --muted:#7a7a7a;
  --stage-top:#fbc488;
  --stage-bottom:#ee93c2;
}
*{margin:0;padding:0;box-sizing:border-box}
html,body{width:1200px;height:1147px;overflow:hidden}
body{background:linear-gradient(180deg,var(--stage-top),var(--stage-bottom));position:relative;font-family:'Dancing Script',cursive;color:var(--ink)}
.page{position:absolute;top:27px;width:359px;height:1090px;background:#fff;overflow:hidden;box-shadow:0 4px 14px rgba(0,0,0,.12)}
.abs{position:absolute}
.hero-bg{left:0;top:32px;width:359px;height:240px;background:var(--hero)}
.hero-photo{left:160px;top:32px;width:199px;height:240px}
.bands{position:absolute;left:0;top:0;width:359px;height:1090px}
.header{left:0;top:0;width:359px;height:32px;background:#fff;display:flex;align-items:center;padding:0 34px}
.brand{display:flex;align-items:center;gap:4px}
.brand-dot{width:12px;height:12px;border-radius:50%;border:1px solid var(--pink)}
.brand-name{font-size:12px;font-weight:700;color:var(--pink);line-height:1}
.brand-tag{font-family:'Poppins',sans-serif;font-size:2.6px;letter-spacing:1px;color:var(--orange);display:block}
.nav{display:flex;gap:13px;margin-left:34px;font-size:5px;color:var(--ink)}
.btn{background:var(--pink);color:#fff;border-radius:3px 9px 3px 3px;font-size:5px;display:flex;align-items:center;justify-content:center}
.book{margin-left:auto;width:43px;height:17px}
.headline{left:28px;top:105px;width:150px;text-align:center;font-size:11px;line-height:1.4;color:var(--pink)}
.cta{left:86px;top:168px;width:41px;height:16px}
.arrow{font-family:'Poppins',sans-serif;font-size:14px;color:var(--orange)}
.arrow.light{color:#fff;opacity:.8}
.dots{left:174px;top:236px;display:flex;gap:2px}
.dots i{width:3px;height:3px;border-radius:50%;background:#c9c9c9}
.dots i.on{background:var(--orange)}
.title{width:359px;text-align:center;font-size:11px;color:var(--orange)}
.card{width:68px;height:113px;background:#fff;box-shadow:0 1px 4px rgba(0,0,0,.15);text-align:center;padding:3px}
.card.active{background:var(--pink);color:#fff}
.card-img{height:49px;width:100%}
.card h3{font-size:5.5px;font-weight:500;margin-top:6px}
.card p{font-size:3.3px;line-height:1.6;color:var(--muted);margin:5px 4px 0;height:17px}
.card.active p{color:#fff}
.outline{border:.6px solid var(--pink);color:var(--pink);background:transparent;width:38px;height:14px;margin:7px auto 0}
.card.active .outline{border-color:#fff;color:#fff}
.story-photo{left:47px;top:487px;width:126px;height:126px;border-radius:50%;border:2px solid var(--orange)}
.story-title{left:206px;top:472px;font-size:11px;color:var(--pink)}
.story-text{left:206px;top:495px;width:120px;font-size:3.5px;line-height:2.2;text-align:justify}
.story-btn{left:206px;top:608px;width:41px;height:16px}
.svc{width:68px;height:71px;border:.7px solid var(--orange);background:#fff;text-align:center;padding-top:8px}
.svc svg{width:18px;height:18px}
.svc h3{font-size:5.5px;font-weight:500;margin-top:2px}
.svc p{font-size:3.2px;line-height:1.6;color:var(--muted);margin:3px 8px 0}
.stars{width:359px;text-align:center;top:873px;font-family:'Poppins',sans-serif;font-size:5px;letter-spacing:.5px;color:var(--orange)}
.quote{left:62px;top:889px;width:236px;text-align:center;font-size:3.6px;line-height:2.2}
.qmark{font-family:'Poppins',sans-serif;font-size:16px;color:var(--pink);line-height:1}
.author{width:359px;text-align:center;top:918px;font-size:6px}
.foot-brand{left:34px;top:1000px;display:flex;flex-direction:column;align-items:flex-start;gap:3px}
.foot-brand .brand-name{font-size:16px;color:var(--orange)}
.foot-brand .brand-dot{width:22px;height:22px;border-color:var(--pink);margin-left:20px}
.foot-col{top:1002px;color:#fff}
.foot-col h4{font-size:7px;font-weight:500;margin-bottom:6px}
.foot-col li{list-style:none;font-size:4px;line-height:2}
.foot-rule{left:34px;top:1060px;width:291px;height:.5px;background:#555}
.copy{left:34px;top:1068px;font-size:4px;color:#fff}
.social{left:290px;top:1068px;display:flex;gap:5px}
.social i{width:4px;height:4px;border-radius:50%;background:var(--orange)}
</style>
</head>
<body>

<svg width="0" height="0" style="position:absolute" aria-hidden="true">
  <defs>
    <linearGradient id="edge" x1="0" y1="0" x2="1" y2="0">
      <stop offset="0" stop-color="#dc3590"/>
      <stop offset="1" stop-color="#f0912c"/>
    </linearGradient>
    <symbol id="person" viewBox="0 0 24 24"><circle cx="12" cy="8" r="4" fill="none" stroke="#dc3590" stroke-width="1.2"/><path d="M5 21c0-5 3-7 7-7s7 2 7 7z" fill="none" stroke="#dc3590" stroke-width="1.2"/></symbol>
    <symbol id="group" viewBox="0 0 24 24"><g fill="none" stroke="#dc3590" stroke-width="1"><circle cx="6" cy="9" r="2.5"/><circle cx="12" cy="8" r="3"/><circle cx="18" cy="9" r="2.5"/><path d="M1 19c0-4 2-6 5-6M23 19c0-4-2-6-5-6M6 20c0-4 3-6 6-6s6 2 6 6z"/></g></symbol>
    <symbol id="crowd" viewBox="0 0 24 24"><g fill="none" stroke="#dc3590" stroke-width="1"><circle cx="9" cy="4" r="2"/><circle cx="15" cy="4" r="2"/><circle cx="5" cy="10" r="2"/><circle cx="12" cy="10" r="2.4"/><circle cx="19" cy="10" r="2"/><path d="M1 21c0-4 2-6 4-6M23 21c0-4-2-6-4-6M6 22c0-4 3-6 6-6s6 2 6 6z"/></g></symbol>
  </defs>
</svg>

<!-- Page variant 1 -->
<section class="page" style="left:26px">
  <div class="abs hero-bg"></div>
  <div class="abs hero-photo" role="img" aria-label="Portrait of a smiling blonde woman touching her face" style="background:linear-gradient(160deg,#e9c9a8,#d9a47d 55%,#c9b3a0)"></div>
  <svg class="bands" viewBox="0 0 359 1090" aria-hidden="true">
    <path d="M0 248C80 280 200 262 359 232L359 1090L0 1090Z" fill="#fff"/>
    <path d="M0 248C80 280 200 262 359 232" fill="none" stroke="url(#edge)" stroke-width="3"/>
    <path d="M0 455C60 472 180 440 359 433L359 623C260 625 150 640 0 648Z" fill="#f7ca91"/>
    <path d="M0 455C60 472 180 440 359 433" fill="none" stroke="url(#edge)" stroke-width="3"/>
    <path d="M359 623C260 625 150 640 0 648" fill="none" stroke="url(#edge)" stroke-width="3"/>
    <path d="M0 828C80 842 220 795 359 800L359 1090L0 1090Z" fill="#f7ca91"/>
    <path d="M0 828C80 842 220 795 359 800" fill="none" stroke="url(#edge)" stroke-width="3"/>
    <path d="M0 978C100 985 250 945 359 950L359 1090L0 1090Z" fill="#262626"/>
    <path d="M0 978C100 985 250 945 359 950" fill="none" stroke="url(#edge)" stroke-width="2"/>
  </svg>
  <header class="abs header">
    <div class="brand"><span class="brand-dot"></span><div><span class="brand-name">Glow Muse</span><span class="brand-tag">CONCIERGE AESTHETICS</span></div></div>
    <nav class="nav"><span>Home</span><span>About</span><span>Services</span><span>Products</span><span>Stories</span></nav>
    <span class="btn book">Book Now</span>
  </header>
  <h1 class="abs headline" style="font-weight:500">Live life on Your Own Time! Glow Muse comes to You</h1>
  <span class="abs btn cta">Get Started</span>
  <span class="abs arrow light" style="left:14px;top:155px">‹</span>
  <span class="abs arrow" style="left:338px;top:155px">›</span>
  <div class="abs dots"><i></i><i class="on"></i><i></i></div>

  <h2 class="abs title" style="top:274px;font-weight:500">Our Products</h2>
  <div class="abs card" style="left:34px;top:298px"><div class="card-img" role="img" aria-label="Fresh green leaves" style="background:linear-gradient(135deg,#6fbf2a,#2f7d12)"></div><h3>Velour</h3><p>First FDA approved formula made only for aesthetics.</p><span class="btn outline">Learn More</span></div>
  <div class="abs card active" style="left:108px;top:298px"><div class="card-img" role="img" aria-label="Man receiving a facial treatment" style="background:linear-gradient(135deg,#eee7e2,#cdbdb3)"></div><h3>Smoothe</h3><p>Still you. With fewer lines!</p><span class="btn outline">Learn More</span></div>
  <div class="abs card" style="left:182px;top:298px"><div class="card-img" role="img" aria-label="Smiling woman at a consultation" style="background:linear-gradient(135deg,#d7dde0,#8a9aa2)"></div><h3>Purelle</h3><p>Pure. For a reason. And the reason is you.</p><span class="btn outline">Learn More</span></div>
  <div class="abs card" style="left:256px;top:298px"><div class="card-img" role="img" aria-label="Green serum in a glass vial" style="background:linear-gradient(135deg,#a9d1b8,#3f9a4e)"></div><h3>Lorem ipsum dolor</h3><p>Lorem ipsum dolor sit amet, consectetur adipiscing elit.</p><span class="btn outline">Learn More</span></div>

  <div class="abs story-photo" role="img" aria-label="Woman receiving a gentle skin assessment" style="background:radial-gradient(circle at 55% 45%,#e8cdbd,#8c8c92 70%)"></div>
  <h2 class="abs story-title" style="font-weight:500">Our Story</h2>
  <p class="abs story-text">How often do we put ourselves last, giving all we have to our families and careers? As a fellow mom, family coordinator and career woman, I quickly realized we all have a right to self care while enjoying our active lifestyles. As a Physician Assistant with over nine years of wound care experience, I saw a fit for my passion and experience: letting people feel their best and look good doing it. My three boys and husband fill my life with unending joy. We are an active family, finding adventure on the football field, ski slopes and mountain bike trails. I find rejuvenation in running, my dogs, coffee and wine. Excited to hear your story!</p>
  <span class="abs btn story-btn">Learn More</span>

  <h2 class="abs title" style="top:679px;font-weight:500">Our Services</h2>
  <div class="abs svc" style="left:67px;top:708px"><svg><use href="#person"/></svg><h3>Private Session</h3><p>The essence of concierge service. Pick the time and place that suits you.</p></div>
  <div class="abs svc" style="left:146px;top:708px"><svg><use href="#group"/></svg><h3>Group Session</h3><p>Bring together family, friends and coworkers with reduced pricing!</p></div>
  <div class="abs svc" style="left:225px;top:708px"><svg><use href="#crowd"/></svg><h3>Muse Party</h3><p>Enjoy time with six or more for wine, hors d'oeuvres and host credits!</p></div>

  <h2 class="abs title" style="top:851px;font-weight:500">Our Inspirations</h2>
  <div class="abs stars">★★★★★</div>
  <span class="abs qmark" style="left:48px;top:878px">“</span>
  <p class="abs quote">“Lorem ipsum dolor sit amet, consectetur adipiscing elit, sed do eiusmod tempor incididunt ut labore et dolore magna aliqua. Ut enim ad minim veniam, quis nostrud exercitation ullamco laboris nisi ut aliquip ex ea commodo consequat.”</p>
  <span class="abs qmark" style="left:300px;top:922px">”</span>
  <span class="abs arrow" style="left:22px;top:906px;font-size:10px;color:var(--ink)">‹</span>
  <span class="abs arrow" style="left:332px;top:906px;font-size:10px;color:var(--ink)">›</span>
  <div class="abs author">John Smith</div>

  <div class="abs foot-brand"><span class="brand-dot"></span><span class="brand-name">Glow Muse</span><span class="brand-tag">CONCIERGE AESTHETICS</span></div>
  <div class="abs foot-col" style="left:145px"><h4>Quick Links</h4><ul><li>Home</li><li>About</li><li>Services</li><li>Products</li><li>Stories</li></ul></div>
  <div class="abs foot-col" style="left:217px"><h4>Service</h4><ul><li>Private Session</li><li>Group Session</li><li>Party</li></ul></div>
  <div class="abs foot-col" style="left:285px"><h4>Conditions</h4><ul><li>Delivery</li><li>Terms of Conditions</li><li>Privacy policy</li></ul></div>
  <div class="abs foot-rule"></div>
  <p class="abs copy">Copyright 2022 Glow Muse &nbsp;|&nbsp; All Rights Reserved</p>
  <div class="abs social"><i></i><i></i><i></i><i></i></div>
</section>

<!-- Page variant 2 -->
<section class="page" style="left:420px">
  <div class="abs hero-bg"></div>
  <div class="abs hero-photo" role="img" aria-label="Portrait of a smiling dark-haired man holding his jaw" style="background:linear-gradient(160deg,#cbb09a,#b98b6c 55%,#a88a78)"></div>
  <svg class="bands" viewBox="0 0 359 1090" aria-hidden="true">
    <path d="M0 248C80 280 200 262 359 232L359 1090L0 1090Z" fill="#fff"/>
    <path d="M0 248C80 280 200 262 359 232" fill="none" stroke="url(#edge)" stroke-width="3"/>
    <path d="M0 455C60 472 180 440 359 433L359 623C260 625 150 640 0 648Z" fill="#f7ca91"/>
    <path d="M0 455C60 472 180 440 359 433" fill="none" stroke="url(#edge)" stroke-width="3"/>
    <path d="M359 623C260 625 150 640 0 648" fill="none" stroke="url(#edge)" stroke-width="3"/>
    <path d="M0 828C80 842 220 795 359 800L359 1090L0 1090Z" fill="#f7ca91"/>
    <path d="M0 828C80 842 220 795 359 800" fill="none" stroke="url(#edge)" stroke-width="3"/>
    <path d="M0 978C100 985 250 945 359 950L359 1090L0 1090Z" fill="#262626"/>
    <path d="M0 978C100 985 250 945 359 950" fill="none" stroke="url(#edge)" stroke-width="2"/>
  </svg>
  <header class="abs header">
    <div class="brand"><span class="brand-dot"></span><div><span class="brand-name">Glow Muse</span><span class="brand-tag">CONCIERGE AESTHETICS</span></div></div>
    <nav class="nav"><span>Home</span><span>About</span><span>Services</span><span>Products</span><span>Stories</span></nav>
    <span class="btn book">Book Now</span>
  </header>
  <h1 class="abs headline" style="font-weight:500">Live life on Your Own Time! Glow Muse comes to You</h1>
  <span class="abs btn cta">Get Started</span>
  <span class="abs arrow light" style="left:14px;top:155px">‹</span>
  <span class="abs arrow" style="left:338px;top:155px">›</span>
  <div class="abs dots"><i></i><i class="on"></i><i></i></div>

  <h2 class="abs title" style="top:274px;font-weight:500">Our Products</h2>
  <div class="abs card" style="left:34px;top:298px"><div class="card-img" role="img" aria-label="Fresh green leaves" style="background:linear-gradient(135deg,#6fbf2a,#2f7d12)"></div><h3>Velour</h3><p>First FDA approved formula made only for aesthetics.</p><span class="btn outline">Learn More</span></div>
  <div class="abs card active" style="left:108px;top:298px"><div class="card-img" role="img" aria-label="Man receiving a facial treatment" style="background:linear-gradient(135deg,#eee7e2,#cdbdb3)"></div><h3>Smoothe</h3><p>Still you. With fewer lines!</p><span class="btn outline">Learn More</span></div>
  <div class="abs card" style="left:182px;top:298px"><div class="card-img" role="img" aria-label="Smiling woman at a consultation" style="background:linear-gradient(135deg,#d7dde0,#8a9aa2)"></div><h3>Purelle</h3><p>Pure. For a reason. And the reason is you.</p><span class="btn outline">Learn More</span></div>
  <div class="abs card" style="left:256px;top:298px"><div class="card-img" role="img" aria-label="Green serum in a glass vial" style="background:linear-gradient(135deg,#a9d1b8,#3f9a4e)"></div><h3>Lorem ipsum dolor</h3><p>Lorem ipsum dolor sit amet, consectetur adipiscing elit.</p><span class="btn outline">Learn More</span></div>

  <div class="abs story-photo" role="img" aria-label="Woman receiving a gentle skin assessment" style="background:radial-gradient(circle at 55% 45%,#e8cdbd,#8c8c92 70%)"></div>
  <h2 class="abs story-title" style="font-weight:500">Our Story</h2>
  <p class="abs story-text">How often do we put ourselves last, giving all we have to our families and careers? As a fellow mom, family coordinator and career woman, I quickly realized we all have a right to self care while enjoying our active lifestyles. As a Physician Assistant with over nine years of wound care experience, I saw a fit for my passion and experience: letting people feel their best and look good doing it. My three boys and husband fill my life with unending joy. We are an active family, finding adventure on the football field, ski slopes and mountain bike trails. I find rejuvenation in running, my dogs, coffee and wine. Excited to hear your story!</p>
  <span class="abs btn story-btn">Learn More</span>

  <h2 class="abs title" style="top:679px;font-weight:500">Our Services</h2>
  <div class="abs svc" style="left:67px;top:708px"><svg><use href="#person"/></svg><h3>Private Session</h3><p>The essence of concierge service. Pick the time and place that suits you.</p></div>
  <div class="abs svc" style="left:146px;top:708px"><svg><use href="#group"/></svg><h3>Group Session</h3><p>Bring together family, friends and coworkers with reduced pricing!</p></div>
  <div class="abs svc" style="left:225px;top:708px"><svg><use href="#crowd"/></svg><h3>Muse Party</h3><p>Enjoy time with six or more for wine, hors d'oeuvres and host credits!</p></div>

  <h2 class="abs title" style="top:851px;font-weight:500">Our Inspirations</h2>
  <div class="abs stars">★★★★★</div>
  <span class="abs qmark" style="left:48px;top:878px">“</span>
  <p class="abs quote">“Lorem ipsum dolor sit amet, consectetur adipiscing elit, sed do eiusmod tempor incididunt ut labore et dolore magna aliqua. Ut enim ad minim veniam, quis nostrud exercitation ullamco laboris nisi ut aliquip ex ea commodo consequat.”</p>
  <span class="abs qmark" style="left:300px;top:922px">”</span>
  <span class="abs arrow" style="left:22px;top:906px;font-size:10px;color:var(--ink)">‹</span>
  <span class="abs arrow" style="left:332px;top:906px;font-size:10px;color:var(--ink)">›</span>
  <div class="abs author">John Smith</div>

  <div class="abs foot-brand"><span class="brand-dot"></span><span class="brand-name">Glow Muse</span><span class="brand-tag">CONCIERGE AESTHETICS</span></div>
  <div class="abs foot-col" style="left:145px"><h4>Quick Links</h4><ul><li>Home</li><li>About</li><li>Services</li><li>Products</li><li>Stories</li></ul></div>
  <div class="abs foot-col" style="left:217px"><h4>Service</h4><ul><li>Private Session</li><li>Group Session</li><li>Party</li></ul></div>
  <div class="abs foot-col" style="left:285px"><h4>Conditions</h4><ul><li>Delivery</li><li>Terms of Conditions</li><li>Privacy policy</li></ul></div>
  <div class="abs foot-rule"></div>
  <p class="abs copy">Copyright 2022 Glow Muse &nbsp;|&nbsp; All Rights Reserved</p>
  <div class="abs social"><i></i><i></i><i></i><i></i></div>
</section>

<!-- Page variant 3 -->
<section class="page" style="left:815px">
  <div class="abs hero-bg"></div>
  <div class="abs hero-photo" role="img" aria-label="Portrait of a smiling woman with curly hair resting her chin on her hand" style="background:linear-gradient(160deg,#b9896a,#9a6446 55%,#a88a78)"></div>
  <svg class="bands" viewBox="0 0 359 1090" aria-hidden="true">
    <path d="M0 248C80 280 200 262 359 232L359 1090L0 1090Z" fill="#fff"/>
    <path d="M0 248C80 280 200 262 359 232" fill="none" stroke="url(#edge)" stroke-width="3"/>
    <path d="M0 455C60 472 180 440 359 433L359 623C260 625 150 640 0 648Z" fill="#f7ca91"/>
    <path d="M0 455C60 472 180 440 359 433" fill="none" stroke="url(#edge)" stroke-width="3"/>
    <path d="M359 623C260 625 150 640 0 648" fill="none" stroke="url(#edge)" stroke-width="3"/>
    <path d="M0 828C80 842 220 795 359 800L359 1090L0 1090Z" fill="#f7ca91"/>
    <path d="M0 828C80 842 220 795 359 800" fill="none" stroke="url(#edge)" stroke-width="3"/>
    <path d="M0 978C100 985 250 945 359 950L359 1090L0 1090Z" fill="#262626"/>
    <path d="M0 978C100 985 250 945 359 950" fill="none" stroke="url(#edge)" stroke-width="2"/>
  </svg>
  <header class="abs header">
    <div class="brand"><span class="brand-dot"></span><div><span class="brand-name">Glow Muse</span><span class="brand-tag">CONCIERGE AESTHETICS</span></div></div>
    <nav class="nav"><span>Home</span><span>About</span><span>Services</span><span>Products</span><span>Stories</span></nav>
    <span class="btn book">Book Now</span>
  </header>
  <h1 class="abs headline" style="font-weight:500">Live life on Your Own Time! Glow Muse comes to You</h1>
  <span class="abs btn cta">Get Started</span>
  <span class="abs arrow light" style="left:14px;top:155px">‹</span>
  <span class="abs arrow" style="left:338px;top:155px">›</span>
  <div class="abs dots"><i></i><i class="on"></i><i></i></div>

  <h2 class="abs title" style="top:274px;font-weight:500">Our Products</h2>
  <div class="abs card" style="left:34px;top:298px"><div class="card-img" role="img" aria-label="Fresh green leaves" style="background:linear-gradient(135deg,#6fbf2a,#2f7d12)"></div><h3>Velour</h3><p>First FDA approved formula made only for aesthetics.</p><span class="btn outline">Learn More</span></div>
  <div class="abs card active" style="left:108px;top:298px"><div class="card-img" role="img" aria-label="Man receiving a facial treatment" style="background:linear-gradient(135deg,#eee7e2,#cdbdb3)"></div><h3>Smoothe</h3><p>Still you. With fewer lines!</p><span class="btn outline">Learn More</span></div>
  <div class="abs card" style="left:182px;top:298px"><div class="card-img" role="img" aria-label="Smiling woman at a consultation" style="background:linear-gradient(135deg,#d7dde0,#8a9aa2)"></div><h3>Purelle</h3><p>Pure. For a reason. And the reason is you.</p><span class="btn outline">Learn More</span></div>
  <div class="abs card" style="left:256px;top:298px"><div class="card-img" role="img" aria-label="Green serum in a glass vial" style="background:linear-gradient(135deg,#a9d1b8,#3f9a4e)"></div><h3>Lorem ipsum dolor</h3><p>Lorem ipsum dolor sit amet, consectetur adipiscing elit.</p><span class="btn outline">Learn More</span></div>

  <div class="abs story-photo" role="img" aria-label="Woman receiving a gentle skin assessment" style="background:radial-gradient(circle at 55% 45%,#e8cdbd,#8c8c92 70%)"></div>
  <h2 class="abs story-title" style="font-weight:500">Our Story</h2>
  <p class="abs story-text">How often do we put ourselves last, giving all we have to our families and careers? As a fellow mom, family coordinator and career woman, I quickly realized we all have a right to self care while enjoying our active lifestyles. As a Physician Assistant with over nine years of wound care experience, I saw a fit for my passion and experience: letting people feel their best and look good doing it. My three boys and husband fill my life with unending joy. We are an active family, finding adventure on the football field, ski slopes and mountain bike trails. I find rejuvenation in running, my dogs, coffee and wine. Excited to hear your story!</p>
  <span class="abs btn story-btn">Learn More</span>

  <h2 class="abs title" style="top:679px;font-weight:500">Our Services</h2>
  <div class="abs svc" style="left:67px;top:708px"><svg><use href="#person"/></svg><h3>Private Session</h3><p>The essence of concierge service. Pick the time and place that suits you.</p></div>
  <div class="abs svc" style="left:146px;top:708px"><svg><use href="#group"/></svg><h3>Group Session</h3><p>Bring together family, friends and coworkers with reduced pricing!</p></div>
  <div class="abs svc" style="left:225px;top:708px"><svg><use href="#crowd"/></svg><h3>Muse Party</h3><p>Enjoy time with six or more for wine, hors d'oeuvres and host credits!</p></div>

  <h2 class="abs title" style="top:851px;font-weight:500">Our Inspirations</h2>
  <div class="abs stars">★★★★★</div>
  <span class="abs qmark" style="left:48px;top:878px">“</span>
  <p class="abs quote">“Lorem ipsum dolor sit amet, consectetur adipiscing elit, sed do eiusmod tempor incididunt ut labore et dolore magna aliqua. Ut enim ad minim veniam, quis nostrud exercitation ullamco laboris nisi ut aliquip ex ea commodo consequat.”</p>
  <span class="abs qmark" style="left:300px;top:922px">”</span>
  <span class="abs arrow" style="left:22px;top:906px;font-size:10px;color:var(--ink)">‹</span>
  <span class="abs arrow" style="left:332px;top:906px;font-size:10px;color:var(--ink)">›</span>
  <div class="abs author">John Smith</div>

  <div class="abs foot-brand"><span class="brand-dot"></span><span class="brand-name">Glow Muse</span><span class="brand-tag">CONCIERGE AESTHETICS</span></div>
  <div class="abs foot-col" style="left:145px"><h4>Quick Links</h4><ul><li>Home</li><li>About</li><li>Services</li><li>Products</li><li>Stories</li></ul></div>
  <div class="abs foot-col" style="left:217px"><h4>Service</h4><ul><li>Private Session</li><li>Group Session</li><li>Party</li></ul></div>
  <div class="abs foot-col" style="left:285px"><h4>Conditions</h4><ul><li>Delivery</li><li>Terms of Conditions</li><li>Privacy policy</li></ul></div>
  <div class="abs foot-rule"></div>
  <p class="abs copy">Copyright 2022 Glow Muse &nbsp;|&nbsp; All Rights Reserved</p>
  <div class="abs social"><i></i><i></i><i></i><i></i></div>
</section>

</body>
</html>
```